Coach/consultant in conflict and challenge needs an enticing flyer

I need a double sided DL flyer design that will describe my work in helping people meet conflict and emotional challenge so they can learn and grow from these difficulties. I want to give a flavour of my style through fresh colours, repeated images used differently (the spiral), and a sense of positivity around conflict and difficulty. I want to attract people who are keen to do things differently and want to engage with creative processes rather than getting stuck in familiar patterns. My work is creative and often includes use of story, images and fables, so I want to convey that as well. I also place the work in a spiritual context, but grounded in practicality so I don't want it to seem New Age or flakey. I want something that seems innovative, professional and intriguing. I've included a sample of something I mocked up in word and also a copy of a flyer for Merle Tavener's Lantern Passage that inspired me to get a DL flyer. I want the design to communicate trust and transformation and engaging with fresh ways of doing things by moving past old habits

Target Market(s)

Mid 30s plus women and men who want to change their approach to conflict and emotional difficulties and are willing to take the creative and challenging journey to do that

Industry/Entity Type

Learn

Colors
acd136
00a990

Requirements
Must have
• a shift in the use of the spiral image,
• use of image of me (Wynne)
• bright fresh colours olours that represent growth and transformation--I've suggested lime green as it suggests a sense of growth
• easy to read text
Nice to have
• Interesting non-traditional fonts perhaps text in a contemporary sans serif and another brush script font (like the Lantern Passage example)
• bleed to the edge and run off the page images or text
Should not have
• anything that represents too much tradition or stuckness

```html
<!DOCTYPE html>
<html lang="en">
<head>
<meta charset="utf-8">
<title>Wynne Ashdown – DL Flyer</title>
<link rel="stylesheet" href="https://fonts.googleapis.com/css2?family=Open+Sans:wght@400;600;700&display=swap">
<style>
  :root {
    --lime: #acd136;
    --lime-soft: #c9e27a;
    --teal: #00a990;
    --teal-soft: #4fc3ae;
    --teal-text: #0f9e86;
    --white: #ffffff;
    --cream: #fdfbe6;
    --artwork: #efe9dc;
    --photo-top: #8f8c7c;
    --photo-mid: #a3866a;
    --photo-low: #cf6636;
    --page: #ffffff;
  }
  * { box-sizing: border-box; margin: 0; padding: 0; }
  html, body { width: 1200px; height: 1000px; overflow: hidden; background: var(--page); }
  body { position: relative; font-family: "Open Sans", sans-serif; color: var(--white); }

  .flyer-side { position: absolute; left: 122px; width: 959px; overflow: hidden; }
  .flyer-front { top: 36px; height: 453px;
    background:
      radial-gradient(ellipse at 55% 55%, rgba(255,255,230,.55), transparent 45%),
      radial-gradient(ellipse at 85% 20%, #a6c93a, transparent 50%),
      linear-gradient(135deg, #bcdc64 0%, var(--lime) 45%, #8dbb2c 100%); }
  .flyer-back { top: 507px; height: 451px;
    background:
      radial-gradient(ellipse at 70% 30%, rgba(240,250,200,.6), transparent 45%),
      linear-gradient(160deg, #c5e170 0%, var(--lime) 50%, #6fb43a 100%); }

  .front-panel { position: absolute; inset: 0;
    background: radial-gradient(ellipse at 20% 20%, #2f9f8a, transparent 60%), linear-gradient(160deg, var(--teal-soft), var(--teal) 70%);
    clip-path: polygon(0 0, 460px 0, 63px 453px, 0 453px); }
  .diagonal-stripe { position: absolute; inset: 0;
    background: linear-gradient(90deg, rgba(255,255,255,.85), rgba(200,240,200,.5));
    clip-path: polygon(448px 0, 462px 0, 70px 453px, 56px 453px); }

  .brand-name { position: absolute; left: 30px; top: 124px; color: var(--cream); line-height: 1; }
  .brand-name .first { display: block; font-size: 62px; font-weight: 400; }
  .brand-name .last { display: block; font-size: 42px; font-weight: 700; margin-top: 4px; }
  .spiral-artwork { position: absolute; left: 35px; top: 300px; width: 103px; height: 93px; background: var(--artwork); }

  .tag-pill { position: absolute; left: 273px; top: 74px; width: 640px; height: 60px;
    border-radius: 30px 0 0 30px;
    background: linear-gradient(90deg, var(--lime-soft), rgba(172,209,54,.2) 60%, transparent);
    border-top: 3px solid #d9806a; }
  .tags { position: absolute; font-weight: 700; color: var(--white); text-shadow: 0 2px 3px rgba(0,0,0,.35); white-space: pre; }
  .tags-front { left: 307px; top: 78px; font-size: 33px; letter-spacing: .3px; }
  .tagline { position: absolute; left: 333px; top: 175px; width: 585px; font-size: 19px; line-height: 29px; color: var(--teal-text); }
  .intro { position: absolute; left: 295px; top: 310px; width: 630px; font-size: 19.5px; line-height: 29px; font-weight: 700; text-shadow: 0 1px 2px rgba(0,0,0,.2); }

  .portrait { position: absolute; inset: 0;
    background: linear-gradient(175deg, var(--photo-top) 0%, var(--photo-mid) 55%, var(--photo-low) 100%);
    clip-path: polygon(0 0, 458px 0, 73px 451px, 0 451px); }
  .back-stripe { position: absolute; inset: 0;
    background: linear-gradient(90deg, rgba(255,255,255,.8), var(--teal-soft));
    clip-path: polygon(452px 0, 464px 0, 80px 451px, 68px 451px); }

  .body-copy { position: absolute; font-size: 16.5px; line-height: 23px; text-align: justify; }
  .body-one { left: 437px; top: 40px; width: 486px; }
  .body-two { left: 320px; top: 194px; width: 603px; }
  .tags-back { left: 233px; top: 281px; font-size: 26px; }

  .name-pill { position: absolute; left: 70px; top: 340px; width: 404px; height: 75px;
    border-radius: 26px; background: var(--teal); box-shadow: 4px 4px 0 var(--lime-soft);
    padding: 5px 0 0 34px; }
  .name-pill .name { font-size: 25px; line-height: 31px; }
  .name-pill .name b { font-size: 21px; font-weight: 700; }
  .name-pill .credentials { font-size: 16.5px; font-weight: 600; }
  .contact { position: absolute; left: 558px; top: 342px; font-size: 16.5px; line-height: 22px; font-style: normal; letter-spacing: -.2px; }
</style>
</head>
<body>
  <section class="flyer-side flyer-front">
    <div class="front-panel"></div>
    <div class="diagonal-stripe"></div>
    <h1 class="brand-name"><span class="first">Wynne</span><span class="last">Ashdown</span></h1>
    <div class="spiral-artwork" role="img" aria-label="Painted brush artwork"></div>
    <div class="tag-pill"></div>
    <p class="tags tags-front"># courage   # listening  # creativity</p>
    <p class="tagline">Challenge, change and conflict are a natural part of life. When we greet them with courage, and listen to what they tell us, we grow in wisdom, resilience and creativity.</p>
    <p class="intro">Wynne Ashdown is a coach, educator and mediator. She works with people who want to harvest the fruits of challenge and conflict so they live life differently.</p>
  </section>

  <section class="flyer-side flyer-back">
    <div class="portrait" role="img" aria-label="Portrait photograph of Wynne Ashdown"></div>
    <div class="back-stripe"></div>
    <p class="body-copy body-one">Consult with Wynne to address challenges in your life, relationship, group or organisation. Through listening, conversation and creative processes, you will discover what your challenge is asking of you. Wynne Ashdown is a skilled facilitator who works to shift people’s responses from reactivity to creativity.</p>
    <p class="body-copy body-two">With many years’ experience in coaching and mentorship, mediation and narrative processes, Wynne supports you to uncover unique responses to difficult situations.</p>
    <p class="tags tags-back"># consultations   # workshops   # speaking   # articles</p>
    <div class="name-pill">
      <p class="name">Wynne <b>Ashdown</b></p>
      <p class="credentials">PhD, MCR, BAppSci, DipHum, AssDipEd</p>
    </div>
    <address class="contact">
      0400 555 018 (m),&nbsp; +61 3 5550 1234 (h)<br>
      wynne@wynneashdown.com,&nbsp; wynneashdown.com<br>
      ABN 12 345 678 90
    </address>
  </section>
</body>
</html>
```